Business Card Design

New business card design

Target Market(s)

Residential & Commercial Property Managers

Industry/Entity Type

Plumbing Services

Contact Information for Business Card

Name - Rowan Keddle, title - Director, Phone Number - 0431 286 517, email - rowan@tbk-plumbing.com.au, Company ABN - 73 215 904 386,

Font styles to use
Sans Serif

Colors
0054AA
0677BA
7BADD7
CADEEF
E8F1F8

```html
<!DOCTYPE html>
<html lang="en">
<head>
<meta charset="utf-8">
<title>TBK Plumbing Services – Business Card</title>
<link href="https://fonts.googleapis.com/css2?family=Montserrat:wght@400;600&display=swap" rel="stylesheet">
<style>
  :root {
    --page-bg: #d9d3cb;
    --card-bg: #ebe4da;
    --card-dark: #2a2c2f;
    --card-dark-soft: #34373a;
    --teal: #2a9bb4;
    --ink: #2b2d30;
    --muted: #c9c4bd;
    --light-text: #d8d2c8;
  }
  html, body {
    margin: 0;
    width: 1200px;
    height: 1047px;
    overflow: hidden;
    background: var(--page-bg);
    font-family: "Montserrat", sans-serif;
  }
  .card {
    position: absolute;
    left: 100px;
    top: 251px;
    width: 1000px;
    height: 544px;
    border-radius: 24px;
    overflow: hidden;
    background: var(--card-bg);
    box-shadow: 0 10px 30px rgba(0,0,0,0.15);
  }
  .accent-line {
    position: absolute;
    left: 0;
    right: 0;
    top: 232px;
    height: 8px;
    background: var(--teal);
  }
  .lower-band {
    position: absolute;
    left: 0;
    right: 0;
    top: 252px;
    bottom: 0;
    background: linear-gradient(180deg, var(--card-dark-soft), var(--card-dark));
  }
  .brand {
    position: absolute;
    right: 46px;
    top: 70px;
    margin: 0;
    font-weight: 400;
    font-size: 46px;
    letter-spacing: 6px;
    color: var(--ink);
    text-align: right;
  }
  .person {
    position: absolute;
    left: 46px;
    top: 296px;
  }
  .person-name {
    margin: 0;
    font-weight: 600;
    font-size: 36px;
    color: var(--teal);
    letter-spacing: 0.5px;
  }
  .person-title {
    margin: 6px 0 0;
    font-size: 23px;
    color: var(--muted);
  }
  .contacts {
    position: absolute;
    left: 44px;
    top: 432px;
    margin: 0;
    padding: 0;
    list-style: none;
    font-size: 25px;
    color: var(--light-text);
  }
  .contacts li {
    display: flex;
    align-items: center;
    gap: 12px;
    height: 38px;
  }
  .contacts svg { width: 22px; height: 22px; }
  .abn {
    position: absolute;
    right: 46px;
    top: 436px;
    text-align: right;
    font-size: 25px;
    line-height: 38px;
    color: var(--light-text);
  }
</style>
</head>
<body>
  <div class="card">
    <div class="accent-line"></div>
    <div class="lower-band" role="img" aria-label="Dark lower band where a flowing dark and teal wave decoration belongs"></div>

    <p class="brand">tbk plumbing services</p>

    <div class="person">
      <h1 class="person-name">Rowan Keddle</h1>
      <p class="person-title">Director</p>
    </div>

    <ul class="contacts">
      <li>
        <svg viewBox="0 0 24 24" aria-hidden="true"><path fill="var(--teal)" d="M6.6 10.8a15 15 0 0 0 6.6 6.6l2.2-2.2a1 1 0 0 1 1-.25 11.4 11.4 0 0 0 3.6.57 1 1 0 0 1 1 1V20a1 1 0 0 1-1 1A17 17 0 0 1 3 4a1 1 0 0 1 1-1h3.5a1 1 0 0 1 1 1c0 1.25.2 2.45.57 3.6a1 1 0 0 1-.25 1z"/></svg>
        <span>0431 286 517</span>
      </li>
      <li>
        <svg viewBox="0 0 24 24" aria-hidden="true"><rect x="2" y="5" width="20" height="14" rx="2" fill="none" stroke="var(--teal)" stroke-width="2"/><path d="M3 6l9 7 9-7" fill="none" stroke="var(--teal)" stroke-width="2"/></svg>
        <span>rowan@tbk-plumbing.com.au</span>
      </li>
    </ul>

    <div class="abn">
      <div>Company ABN</div>
      <div>- 73 215 904 386</div>
    </div>
  </div>
</body>
</html>
```